Nivel Crest - Powerpoint Templates

We are a consultancy to help builders to optimize their planning in order to save building costs. For that reason we need templates for teasers and presentations where we offer our services, show our team and their capacities and present workflows, organization charts, price lists etc.

```html
<!DOCTYPE html>
<html lang="en">
<head>
<meta charset="utf-8">
<title>Nivel Crest – Presentation Templates</title>
<link href="https://fonts.googleapis.com/css2?family=Orbitron:wght@600;700&family=Montserrat:wght@400;500;600;700&display=swap" rel="stylesheet">
<style>
:root{
  --page:#f6f6f7;
  --slate-1:#4a4b50;
  --slate-2:#2a2b2f;
  --slate-3:#1c1c1f;
  --gold:#c8923a;
  --gold-light:#f2c866;
  --grey:#a9a9ab;
  --chip:#9d9d9f;
  --white:#ffffff;
  --ink:#2c2c2e;
  --muted:#5e5e62;
  --green:#3aa54a;
}
*{box-sizing:border-box;margin:0;padding:0}
html,body{width:1200px;height:1162px;overflow:hidden;background:var(--page)}
body{position:relative;font-family:"Montserrat",sans-serif;color:var(--white)}
.display{font-family:"Orbitron",sans-serif;font-weight:700;letter-spacing:.06em;text-transform:uppercase}

.slide{position:absolute;width:542px;height:305px;overflow:hidden;
  background:radial-gradient(ellipse 70% 60% at 55% 35%,var(--slate-1),var(--slate-2) 60%,var(--slate-3));}
.s1{left:42px;top:64px}.s2{left:620px;top:64px}
.s3{left:42px;top:420px}.s4{left:620px;top:420px}
.s5{left:42px;top:769px}.s6{left:620px;top:769px}

.page-tab{position:absolute;right:0;top:272px;width:56px;height:17px;background:var(--chip);
  color:var(--slate-3);font-size:5.5px;display:flex;align-items:center;justify-content:center}
.brand-mark{position:absolute;left:21px;top:264px;font-family:"Orbitron",sans-serif;font-weight:700;
  font-size:8px;letter-spacing:.08em;color:var(--white);text-transform:uppercase}

.header{position:absolute;top:30px;left:0;right:0;height:10px;display:flex;align-items:center}
.header .rail{height:10px;border-top:1.5px solid var(--gold);border-bottom:1.5px solid var(--gold);flex:1}
.header .rail.left{border-right:1.5px solid var(--gold)}
.header .rail.right{border-left:1.5px solid var(--gold)}
.header h2{font-size:12.5px;padding:0 11px;white-space:nowrap;color:var(--white)}

/* cover */
.hero-band{position:absolute;left:0;top:105px;width:414px;height:103px;background:rgba(70,71,76,.75);
  border-top:1.5px solid var(--gold);border-bottom:1.5px solid var(--gold)}
.hero-halo{position:absolute;left:296px;top:50px;width:300px;height:300px;border-radius:50%;background:#68696d}
.hero-photo{position:absolute;left:316px;top:0;width:226px;height:305px;
  background:linear-gradient(180deg,#b79784 0 32%,#1f2840 32% 100%);border-radius:110px 0 0 0}
.hero-name{position:absolute;left:40px;top:158px;width:200px;text-align:center}
.hero-name .name{font-size:15px;color:var(--gold-light)}
.hero-name .tag{font-size:6.5px;letter-spacing:.3em;color:var(--gold-light);margin-top:4px;font-family:"Orbitron",sans-serif;font-weight:600;text-transform:uppercase}
.hero-url{position:absolute;left:28px;top:279px;font-size:7px;color:var(--white);font-family:"Orbitron",sans-serif;font-weight:700;letter-spacing:.04em}

/* services */
.service{position:absolute;top:92px;width:120px;text-align:center}
.service .photo{height:120px;border:3px solid var(--gold);border-radius:12px}
.service h3{font-size:8.5px;margin-top:10px}

/* team */
.member{position:absolute;top:75px;width:118px;height:163px;border-radius:12px;
  background:linear-gradient(180deg,#ffffff,#d5d5d7);color:var(--ink);text-align:center;padding:0 9px}
.member .avatar{width:80px;height:80px;border-radius:50%;border:1.5px solid var(--gold);margin:-12px auto 0}
.member h3{font-size:6px;margin-top:10px}
.member .role{font-size:5.5px;margin-top:1px}
.member p{font-size:4.6px;line-height:1.75;color:var(--muted);margin-top:9px;text-align:justify;text-align-last:center}

/* workflow */
.flow{position:absolute;left:0;top:0}
.step{position:absolute;width:66px}
.step h3{font-size:6px;line-height:1.5;color:var(--white)}
.step p{font-size:5.8px;line-height:1.55;color:#d8d8da;margin-top:6px}

/* chart */
.legend{position:absolute;left:296px;top:96px;list-style:none}
.legend li{display:flex;align-items:center;height:26px}
.legend .pct{width:34px;text-align:right;font-family:"Orbitron",sans-serif;font-weight:700;font-size:11px}
.legend .sw{width:13px;height:10px;margin:0 8px;border:1px solid #d9d9d9}
.legend .lbl{font-family:"Orbitron",sans-serif;font-weight:700;font-size:9.5px;letter-spacing:.04em;text-transform:uppercase}

/* prices */
.plan{position:absolute;top:86px;width:108px;height:157px;background:var(--white);
  border:1.5px solid var(--gold-light);padding:9px 9px;color:var(--ink)}
.plan h3{font-size:5.5px;color:var(--ink)}
.plan .price{font-family:"Orbitron",sans-serif;font-weight:700;font-size:10px;color:var(--gold);margin-top:5px}
.plan .price small{font-size:4.5px}
.plan .desc{font-family:"Montserrat",sans-serif;font-size:5.2px;line-height:1.55;color:var(--muted);margin-top:6px}
.plan ul{list-style:none;margin-top:7px}
.plan li{font-family:"Montserrat",sans-serif;font-size:7px;display:flex;align-items:center;gap:5px;height:14px;padding-left:2px}
.plan li .tick{width:6px;height:6px;border-radius:50%;background:var(--green);position:relative;flex:none}
.plan li .tick::after{content:"";position:absolute;left:1.8px;top:.9px;width:1.5px;height:3px;border:solid #fff;border-width:0 .8px .8px 0;transform:rotate(45deg)}
</style>
</head>
<body>

<section class="slide s1">
  <div class="hero-band"></div>
  <div class="hero-halo"></div>
  <div class="hero-photo" role="img" aria-label="Portrait of a senior consultant in a dark suit"></div>
  <div class="hero-name">
    <div class="name display">Nivel Crest</div>
    <div class="tag">Plan smart build lean</div>
  </div>
  <div class="hero-url">WWW.NIVELCREST.COM</div>
  <div class="page-tab display">Page 1</div>
</section>

<section class="slide s2">
  <div class="header"><div class="rail left"></div><h2 class="display">Our Services</h2><div class="rail right"></div></div>
  <div class="service" style="left:50px"><div class="photo" role="img" aria-label="Businessman signing documents at a desk" style="background:linear-gradient(160deg,#c9ccd0,#2f3c5a)"></div><h3 class="display">Optimize</h3></div>
  <div class="service" style="left:214px"><div class="photo" role="img" aria-label="Two people reviewing plans on a tablet" style="background:linear-gradient(160deg,#6b5a4a,#26272b)"></div><h3 class="display">Planning</h3></div>
  <div class="service" style="left:379px"><div class="photo" role="img" aria-label="Team meeting around an office table" style="background:linear-gradient(160deg,#9aa49a,#b89a6a)"></div><h3 class="display">Building Costs</h3></div>
  <div class="brand-mark">Nivel Crest</div>
  <div class="page-tab display">Page 2</div>
</section>

<section class="slide s3">
  <div class="header"><div class="rail left"></div><h2 class="display">Our Team</h2><div class="rail right"></div></div>
  <div class="member" style="left:23px"><div class="avatar" role="img" aria-label="Team member portrait" style="background:linear-gradient(#6a5a48,#8e8e92)"></div><h3 class="display">Tom Hale</h3><div class="role">Cheif Executive</div><p>Lorem ipsum dolor sit amet, consectetur adipiscing elit, sed do eiusmod tempor incididunt ut labore et dolore magna aliqua. Quis ipsum suspendisse ultrices gravida.</p></div>
  <div class="member" style="left:149px"><div class="avatar" role="img" aria-label="Team member portrait" style="background:linear-gradient(#3c4a66,#e6dccb)"></div><h3 class="display">Anna Roth</h3><div class="role">Cheif Executive</div><p>Lorem ipsum dolor sit amet, consectetur adipiscing elit, sed do eiusmod tempor incididunt ut labore et dolore magna aliqua. Quis ipsum suspendisse ultrices gravida.</p></div>
  <div class="member" style="left:275px"><div class="avatar" role="img" aria-label="Team member portrait" style="background:linear-gradient(#f2f2f2,#d8d8d8)"></div><h3 class="display">Leo Brandt</h3><div class="role">Cheif Executive</div><p>Lorem ipsum dolor sit amet, consectetur adipiscing elit, sed do eiusmod tempor incididunt ut labore et dolore magna aliqua. Quis ipsum suspendisse ultrices gravida.</p></div>
  <div class="member" style="left:401px"><div class="avatar" role="img" aria-label="Team member portrait" style="background:linear-gradient(#f4f4f4 55%,#1e1e22)"></div><h3 class="display">Paul Weber</h3><div class="role">Cheif Executive</div><p>Lorem ipsum dolor sit amet, consectetur adipiscing elit, sed do eiusmod tempor incididunt ut labore et dolore magna aliqua. Quis ipsum suspendisse ultrices gravida.</p></div>
  <div class="brand-mark">Nivel Crest</div>
  <div class="page-tab display">Page 3</div>
</section>

<section class="slide s4">
  <div class="header"><div class="rail left"></div><h2 class="display">Capacities and Present Workflows</h2><div class="rail right"></div></div>
  <svg class="flow" width="542" height="305" viewBox="0 0 542 305" fill="none">
    <path d="M0 158 C30 132 50 128 66 128 C110 126 130 132 156 142 C200 160 230 170 263 166 C300 162 330 140 362 137 C400 134 430 132 454 137 C490 142 520 162 542 172" stroke="#c8923a" stroke-width="1"/>
    <g fill="#f2c866"><circle cx="66" cy="128" r="7"/><circle cx="156" cy="142" r="7"/><circle cx="263" cy="166" r="7"/><circle cx="362" cy="137" r="7"/><circle cx="454" cy="137" r="7"/></g>
    <g stroke="#fff" stroke-width="1" stroke-linecap="round" stroke-linejoin="round">
      <rect x="59" y="98" width="16" height="12"/><path d="M75 102h6l4 4v4h-10"/><circle cx="64" cy="111" r="2"/><circle cx="80" cy="111" r="2"/>
      <circle cx="160" cy="111" r="6"/><path d="M157 118h6M158 121h4M150 104l-3-2M170 104l3-2M160 100v-4"/>
      <circle cx="264" cy="136" r="11"/><circle cx="264" cy="136" r="7"/><circle cx="264" cy="136" r="3"/>
      <rect x="352" y="100" width="18" height="18" rx="2"/><path d="M361 100v18M352 109h18"/>
      <path d="M442 108l7-5 6 4 6-4 7 5-7 8-6 3-6-3z"/><path d="M449 103l6 6 6-6"/>
    </g>
  </svg>
  <div class="step" style="left:59px;top:150px"><h3 class="display">On-Time<br>Delivery</h3><p>Lorem ipsum dolor sit amet, consectetur adipiscing elit, sed do eiusmod tempor</p></div>
  <div class="step" style="left:149px;top:174px"><h3 class="display">Capability</h3><p>Lorem ipsum dolor sit amet, consectetur adipiscing elit, sed do eiusmod tempor</p></div>
  <div class="step" style="left:256px;top:189px"><h3 class="display">Coverage</h3><p>Lorem ipsum dolor sit amet, consectetur adipiscing elit, sed do eiusmod tempor</p></div>
  <div class="step" style="left:356px;top:158px"><h3 class="display">Contribution</h3><p>Lorem ipsum dolor sit amet, consectetur adipiscing elit, sed do eiusmod tempor</p></div>
  <div class="step" style="left:448px;top:171px"><h3 class="display">Commitment</h3><p>Lorem ipsum dolor sit amet, consectetur adipiscing elit, sed do eiusmod tempor</p></div>
  <div class="brand-mark">Nivel Crest</div>
  <div class="page-tab display">Page 4</div>
</section>

<section class="slide s5">
  <div class="header"><div class="rail left"></div><h2 class="display">Organization Charts</h2><div class="rail right"></div></div>
  <svg width="542" height="305" viewBox="0 0 542 305" style="position:absolute;left:0;top:0">
    <g transform="translate(151 166)" stroke="#26272b" stroke-width="4" stroke-linejoin="round">
      <path d="M0 0L0 -83A83 83 0 0 1 67.1 -48.8Z" fill="#f2c866"/>
      <path d="M0 0L67.1 -48.8A83 83 0 0 1 0 83Z" fill="#a9a9ab"/>
      <path d="M0 0L0 83A83 83 0 0 1 -67.1 48.8Z" fill="#ffffff"/>
      <path d="M0 0L-67.1 48.8A83 83 0 0 1 -48.8 -67.1Z" fill="#4a4b50"/>
      <path d="M0 0L-48.8 -67.1A83 83 0 0 1 0 -83Z" fill="#c8923a"/>
    </g>
    <g font-family="Orbitron, sans-serif" font-weight="700" font-size="11" fill="#1c1c1f">
      <text x="120" y="108">10%</text><text x="167" y="112">15%</text>
      <text x="87" y="158" fill="#ffffff">25%</text><text x="179" y="185">35%</text>
      <text x="119" y="212">15%</text>
    </g>
  </svg>
  <ul class="legend">
    <li><span class="pct">35%</span><span class="sw" style="background:var(--grey)"></span><span class="lbl">– On-Time Delivery</span></li>
    <li><span class="pct">25%</span><span class="sw" style="background:var(--slate-1)"></span><span class="lbl">– Capability</span></li>
    <li><span class="pct">15%</span><span class="sw" style="background:var(--gold-light)"></span><span class="lbl">– Coverage</span></li>
    <li><span class="pct">15%</span><span class="sw" style="background:var(--white)"></span><span class="lbl">– Contribution</span></li>
    <li><span class="pct">10%</span><span class="sw" style="background:var(--gold)"></span><span class="lbl">– Commitment</span></li>
  </ul>
  <div class="brand-mark">Nivel Crest</div>
  <div class="page-tab display">Page 5</div>
</section>

<section class="slide s6">
  <div class="header"><div class="rail left"></div><h2 class="display">Price List</h2><div class="rail right"></div></div>
  <div class="plan" style="left:61px"><h3 class="display">Basic</h3><div class="price">$99.00/<small>MONTH</small></div><p class="desc">Lorem ipsum dolor sit amet, consectetur adipiscing elit, sed do eiusmod tempor.</p><ul><li><span class="tick"></span>Lorem Ipsum</li><li><span class="tick"></span>Lorem Ipsum</li><li><span class="tick"></span>Lorem Ipsum</li><li><span class="tick"></span>Lorem Ipsum</li><li><span class="tick"></span>Lorem Ipsum</li></ul></div>
  <div class="plan" style="left:216px"><h3 class="display">Popular</h3><div class="price">$149.00/<small>MONTH</small></div><p class="desc">Lorem ipsum dolor sit amet, consectetur adipiscing elit, sed do eiusmod tempor.</p><ul><li><span class="tick"></span>Lorem Ipsum</li><li><span class="tick"></span>Lorem Ipsum</li><li><span class="tick"></span>Lorem Ipsum</li><li><span class="tick"></span>Lorem Ipsum</li><li><span class="tick"></span>Lorem Ipsum</li></ul></div>
  <div class="plan" style="left:371px"><h3 class="display">Enterprise</h3><div class="price">$199.00/<small>MONTH</small></div><p class="desc">Lorem ipsum dolor sit amet, consectetur adipiscing elit, sed do eiusmod tempor.</p><ul><li><span class="tick"></span>Lorem Ipsum</li><li><span class="tick"></span>Lorem Ipsum</li><li><span class="tick"></span>Lorem Ipsum</li><li><span class="tick"></span>Lorem Ipsum</li><li><span class="tick"></span>Lorem Ipsum</li></ul></div>
  <div class="brand-mark">Nivel Crest</div>
  <div class="page-tab display">Page 6</div>
</section>

</body>
</html>
```